Business Card: RW Office Partners - Your organised problem solver

Business Name: RW Office Partners
Website: www.rwofficepartners.com.au
Email: marisol@rwofficepartners.com.au
Mobile: 61 482 907 236
Facebook: @rwofficepartners
Instrgram: @rwofficepartners

Brading Colours:
HEX
#986474
#ddccd3
#7a8498
#c9d8e4
#000000
#ffffff

Tag Line: Your organised problem solver

Link to DRAFT website:
https://deskhelpcollective.wixsite.com/rw-office-partners

About Page from the website:
My name is Marisol Wrenfield, and I would love to assist you to become more productive in your day to day and achieve your business and personal goals.
My mission is to give you time, time to work on the important tasks of your business or to be able to spend more time with your family. I will take on the tasks you don’t have time for, don’t know well or simply don’t like to do.
I have an extensive background in Administration, Tender Coordination, Document Control, WHS and Quality Management working primarily in the Construction, Mining and Corporate World.
I am passionate about being organised, having order and making things in your life (and mine) easier! I love to watch something unfold and grow into something amazing! I am known for being the go-to problem solver, the organiser of all things, producing high standards of work even under pressure. I’m also a confident communicator, and I understand that you’re busy running your business.

Target Market(s)

Small to Medium Business who require assistance in their business by a virtual assistant.

Industry/Entity Type

Virtual Assistant

Contact Information for Business Card

Mobile: 61 482 907 236

Font styles to use
Sans Serif

Colors
ffffff

Requirements
Must have
• Branding Colours as outlined.
Contact Details as outlined.
Logo as provided.
Proper contact details - mobile, facebook, instragm, website.
Simple, Elegant, very clean looking.
Should not have
• Note cute with pictures.
Not too girly as still want to market to construction companies.

```html
<!DOCTYPE html>
<html lang="en">
<head>
<meta charset="utf-8">
<title>RW Office Partners – Business Card</title>
<link rel="stylesheet" href="https://fonts.googleapis.com/css2?family=Roboto:wght@400;500;700&display=swap">
<style>
  :root {
    --stage: #3b3b3d;
    --card: #1f1e22;
    --mauve: #986474;
    --slate: #7a8498;
    --ice: #c9d8e4;
    --white: #ffffff;
  }
  * { box-sizing: border-box; margin: 0; padding: 0; }
  html, body { width: 799px; height: 1200px; overflow: hidden; }
  body {
    background: var(--stage);
    font-family: "Roboto", Arial, sans-serif;
    color: var(--white);
    position: relative;
  }
  .card {
    position: absolute;
    left: 80px;
    width: 640px;
    height: 366px;
    background: var(--card);
    border-radius: 4px;
    box-shadow: 0 14px 30px rgba(0,0,0,.45);
    overflow: hidden;
  }
  .card--front { top: 120px; }
  .card--back { top: 714px; }

  /* front */
  .front-brand {
    position: absolute;
    left: 0; right: 0; top: 110px;
    text-align: center;
  }
  .brand-name {
    font-weight: 500;
    font-size: 46px;
    letter-spacing: 2px;
    text-transform: uppercase;
    color: var(--mauve);
    line-height: 1;
  }
  .brand-rule {
    width: 260px;
    height: 1px;
    background: var(--slate);
    margin: 20px auto 0;
  }
  .socials {
    position: absolute;
    left: 0; right: 0;
    display: flex;
    justify-content: center;
    gap: 26px;
    font-size: 19px;
  }
  .card--front .socials { top: 290px; }
  .card--back .socials { top: 300px; }
  .social { display: flex; align-items: center; gap: 8px; }
  .social-mark {
    width: 13px; height: 13px;
    background: var(--mauve);
    border-radius: 2px;
  }
  .social-mark--round { border-radius: 50%; }

  /* back */
  .back-brand {
    position: absolute;
    left: 48px; top: 70px;
    width: 250px;
    font-weight: 700;
    font-size: 40px;
    line-height: 1.05;
    color: var(--mauve);
    text-transform: uppercase;
  }
  .person {
    position: absolute;
    left: 330px; top: 86px;
  }
  .person-name {
    font-weight: 700;
    font-size: 22px;
    color: var(--mauve);
  }
  .person-role { font-size: 16px; margin-top: 2px; }
  .contacts { list-style: none; margin-top: 14px; font-size: 16px; }
  .contacts li { display: flex; align-items: center; gap: 10px; margin-bottom: 5px; }
  .contacts svg { width: 14px; height: 14px; fill: none; stroke: var(--mauve); stroke-width: 1.6; }
  .back-rule {
    position: absolute;
    top: 312px;
    width: 80px;
    height: 1px;
    background: var(--ice);
    opacity: .7;
  }
  .back-rule--left { left: 0; }
  .back-rule--right { right: 0; }
</style>
</head>
<body>
  <section class="card card--front">
    <div class="front-brand">
      <div class="brand-name">RW Office Partners</div>
      <div class="brand-rule"></div>
    </div>
    <div class="socials">
      <span class="social"><span class="social-mark"></span>@rwofficepartners</span>
      <span class="social"><span class="social-mark social-mark--round"></span>@rwofficepartners</span>
    </div>
  </section>

  <section class="card card--back">
    <div class="back-brand">RW Office Partners</div>
    <div class="person">
      <div class="person-name">Marisol Wrenfield</div>
      <div class="person-role">Virtual Assistant</div>
      <ul class="contacts">
        <li><svg viewBox="0 0 16 16"><path d="M4 2l2.5 3-1.5 1.5a8 8 0 0 0 4.5 4.5L11 9.5l3 2.5-1.5 2A10 10 0 0 1 2 3.5z"/></svg>61 482 907 236</li>
        <li><svg viewBox="0 0 16 16"><rect x="1.5" y="3.5" width="13" height="9"/><path d="M1.5 3.5L8 9l6.5-5.5"/></svg>marisol@rwofficepartners.com.au</li>
        <li><svg viewBox="0 0 16 16"><circle cx="8" cy="8" r="6.5"/><path d="M1.5 8h13M8 1.5c-3 3.5-3 9.5 0 13M8 1.5c3 3.5 3 9.5 0 13"/></svg>www.rwofficepartners.com.au</li>
      </ul>
    </div>
    <div class="back-rule back-rule--left"></div>
    <div class="back-rule back-rule--right"></div>
    <div class="socials">
      <span class="social"><span class="social-mark"></span>@rwofficepartners</span>
      <span class="social"><span class="social-mark social-mark--round"></span>@rwofficepartners</span>
    </div>
  </section>
</body>
</html>
```